Business Card Design - Amberfield Court

We are looking at a new design for our business cards that has a modern and professional look. We run a residential aged care facility focussing on the care of residents. The cards will be used for potential clients, consultants and business opportunities in this sector. Blue and white is our main colours and would to see these colours incorporated in the design.
Industry/Entity Type
Business
Contact Information for Business Card
Amberfield Court, Darren Walsh, dwalsh@amberfieldcourt.com.au, Finance Manager, 0472 639 208, BCom, 37 Marrabel Crescent, Brindle Vale, Qld 4093.
Look and feel
Each slider illustrates characteristics of the customer's brand and the style your logo design should communicate.

```html
<!DOCTYPE html>
<html lang="en">
<head>
<meta charset="utf-8">
<title>Amberfield Court – Business Card</title>
<link rel="stylesheet" href="https://fonts.googleapis.com/css2?family=Source+Sans+3:wght@400;600&display=swap">
<style>
  :root {
    --backdrop: #101010;
    --card: #dfe6eb;
    --brand-blue: #4a7a94;
    --ink: #1e2328;
    --rule: #b9c3ca;
  }
  * { box-sizing: border-box; margin: 0; padding: 0; }
  html, body {
    width: 1200px; height: 900px; overflow: hidden;
    background: var(--backdrop);
    font-family: "Source Sans 3", "Myriad Pro", Arial, sans-serif;
  }
  .card {
    position: absolute;
    top: 307px;
    height: 270px;
    background: var(--card);
    border-radius: 10px;
  }
  .card--front { left: 150px; width: 437px; }
  .card--back { left: 609px; width: 439px; }

  .brand-mark {
    position: absolute;
    display: flex;
    flex-direction: column;
    align-items: center;
    color: var(--brand-blue);
    font-weight: 600;
    letter-spacing: 0.06em;
    text-transform: uppercase;
  }
  .brand-mark__dot {
    border-radius: 50%;
    background: var(--brand-blue);
  }
  .card--front .brand-mark { left: 30px; top: 96px; width: 170px; gap: 12px; font-size: 15px; }
  .card--front .brand-mark__dot { width: 48px; height: 48px; }
  .card--back .brand-mark { left: 0; right: 0; top: 64px; gap: 16px; font-size: 26px; }
  .card--back .brand-mark__dot { width: 86px; height: 86px; }

  .divider {
    position: absolute;
    left: 205px; top: 70px;
    width: 1px; height: 142px;
    background: var(--rule);
  }
  .contact {
    position: absolute;
    left: 222px; top: 66px;
    color: var(--ink);
    font-size: 12.5px;
    line-height: 18px;
  }
  .contact__name {
    color: var(--brand-blue);
    font-size: 17px;
    font-weight: 600;
    line-height: 22px;
  }
  .contact__credential { font-size: 12px; }
  .contact__address { margin-top: 16px; }
  .contact__lines { margin-top: 15px; }
  .contact__line { display: flex; align-items: center; gap: 5px; }
  .contact__line svg { width: 9px; height: 9px; fill: var(--brand-blue); }
</style>
</head>
<body>
  <section class="card card--front" aria-label="Business card front">
    <div class="brand-mark">
      <span class="brand-mark__dot"></span>
      <span class="brand-mark__name">Amberfield Court</span>
    </div>
    <div class="divider"></div>
    <div class="contact">
      <p class="contact__name">Darren Walsh, <span class="contact__credential">BCom</span></p>
      <p class="contact__title">Finance Manager</p>
      <p class="contact__address">37 Marrabel Crescent,<br>Brindle Vale, Qld 4093</p>
      <div class="contact__lines">
        <p class="contact__line">
          <svg viewBox="0 0 10 10" aria-hidden="true"><path d="M2 0.5 L3.6 2.6 L2.8 3.6 Q4 6 6.4 7.2 L7.4 6.4 L9.5 8 L8.4 9.6 Q3.8 9 0.4 1.6 Z"/></svg>
          0472 639 208
        </p>
        <p class="contact__line">
          <svg viewBox="0 0 10 10" aria-hidden="true"><path d="M0.5 2 H9.5 V8.5 H0.5 Z M1 2.4 L5 5.6 L9 2.4" stroke="#dfe6eb" stroke-width="0.8"/></svg>
          dwalsh@amberfieldcourt.com.au
        </p>
      </div>
    </div>
  </section>

  <section class="card card--back" aria-label="Business card back">
    <div class="brand-mark">
      <span class="brand-mark__dot"></span>
      <span class="brand-mark__name">Amberfield Court</span>
    </div>
  </section>
</body>
</html>
```